Ridgeline Journeys business card

please see website
www.ridgelinejourneys.comau

info needed on card
Curtis Halvey
Ph
email
Adventure Riding GPS trails

please use my logo and colours off my site

Curtis Halvey
curtis@ridgelinejourneys.com

```html
<!DOCTYPE html>
<html lang="en">
<head>
<meta charset="utf-8">
<title>Ridgeline Journeys business card</title>
<link rel="stylesheet" href="https://fonts.googleapis.com/css2?family=Open+Sans:wght@400;600;700;800&display=swap">
<style>
  :root {
    --stage: #ecebe8;
    --ink: #0b0b0b;
    --paper: #ffffff;
    --yellow: #ffd000;
    --yellow-light: #ffe23a;
    --yellow-text: #ffd21a;
    --white-text: #ffffff;
    --body-text: #1a1a1a;
  }
  * { margin: 0; padding: 0; box-sizing: border-box; }
  html, body {
    width: 1200px;
    height: 900px;
    overflow: hidden;
    background: var(--stage);
    font-family: "Open Sans", Arial, sans-serif;
  }
  .canvas { position: relative; width: 1200px; height: 900px; }

  .card {
    position: absolute;
    overflow: hidden;
    box-shadow: 0 3px 10px rgba(0,0,0,0.18);
  }

  /* Front side */
  .card-front {
    left: 238px; top: 62px;
    width: 555px; height: 343px;
    background: linear-gradient(180deg, var(--yellow) 0%, var(--yellow) 42%, var(--yellow-light) 42%, var(--yellow-light) 100%);
  }
  .front-panel { position: absolute; inset: 0; width: 100%; height: 100%; }
  .holder-name {
    position: absolute; left: 35px; top: 56px;
    font-size: 17px; font-weight: 600; color: var(--white-text);
    white-space: nowrap;
  }
  .holder-name .first { color: var(--yellow-text); }
  .contact-list {
    position: absolute; left: 37px; top: 97px;
    list-style: none;
  }
  .contact-list li {
    display: flex; align-items: center; gap: 8px;
    height: 20px;
    font-size: 13px; color: var(--white-text);
    white-space: nowrap;
  }
  .contact-list svg { width: 10px; height: 10px; flex: none; }
  .front-name {
    position: absolute; right: 24px; top: 232px;
    font-size: 34px; line-height: 40px; font-weight: 800;
    color: var(--ink); text-transform: uppercase; text-align: left;
    white-space: nowrap;
  }

  /* Back side */
  .card-back {
    left: 457px; top: 518px;
    width: 560px; height: 344px;
    background: var(--paper);
  }
  .back-mark {
    position: absolute; left: 128px; top: 124px;
    width: 92px; height: 92px; border-radius: 50%;
    background: var(--yellow);
  }
  .back-name {
    position: absolute; left: 246px; top: 136px;
    font-size: 29px; line-height: 36px; font-weight: 800;
    color: var(--ink); text-transform: uppercase;
    white-space: nowrap;
  }
  .back-tagline {
    position: absolute; left: 247px; top: 220px;
    font-size: 16px; font-weight: 700; color: var(--body-text);
    white-space: nowrap;
  }
  .back-web {
    position: absolute; left: 0; right: 0; top: 294px;
    text-align: center; font-size: 14px; color: var(--body-text);
  }
</style>
</head>
<body>
<div class="canvas">

  <section class="card card-front" aria-label="Business card front">
    <svg class="front-panel" viewBox="0 0 555 343" aria-hidden="true">
      <polygon points="0,0 305,0 232,343 0,343" fill="var(--ink)"/>
    </svg>
    <p class="holder-name"><span class="first">Curtis</span> Halvey</p>
    <ul class="contact-list">
      <li>
        <svg viewBox="0 0 10 10"><path d="M1 3 Q5 0 9 3 L8 4.5 L6.5 3.8 L6.5 3 Q5 2.6 3.5 3 L3.5 3.8 L2 4.5 Z M2.5 5 H7.5 L8.5 9 H1.5 Z" fill="var(--yellow-text)"/></svg>
        044-555 010 246
      </li>
      <li>
        <svg viewBox="0 0 10 10"><rect x="0.5" y="2" width="9" height="6.5" fill="var(--yellow-text)"/><path d="M0.5 2 L5 5.8 L9.5 2" fill="none" stroke="var(--ink)" stroke-width="0.9"/></svg>
        curtis@ridgelinejourneys.com
      </li>
      <li>
        <svg viewBox="0 0 10 10"><g fill="none" stroke="var(--yellow-text)" stroke-width="1.4"><rect x="0.8" y="4.2" width="5" height="2.6" rx="1.3" transform="rotate(-45 3.3 5.5)"/><rect x="4.2" y="3.2" width="5" height="2.6" rx="1.3" transform="rotate(-45 6.7 4.5)"/></g></svg>
        www.ridgelinejourneys.comau
      </li>
    </ul>
    <p class="front-name">Ridgeline<br>Journeys</p>
  </section>

  <section class="card card-back" aria-label="Business card back">
    <div class="back-mark" aria-hidden="true"></div>
    <p class="back-name">Ridgeline<br>Journeys</p>
    <p class="back-tagline">Adventure Riding GPS trails</p>
    <p class="back-web">www.ridgelinejourneys.comau</p>
  </section>

</div>
</body>
</html>
```